Flyer Design Project

I need to create a flyer to advertise an Luxury Self Catering Apartment Complex in a Ski Resort in Europe. The development offers luxury accommodation to those who are on a budget.

Below is what needs to be included and a basic layout design idea i had that can be changed. The information is important. Hoping to get it on a flyer sized 21.6 x 14 cm

Title - 'Luxury Self Catering Ski Apartments For Rent'
Sub Title - 'Located 200m from Gondola, Restaurants and Bars'

Studio - Sleeps 1-2 - From only £200 per week
1 Bed - Sleeps 2-4 - From only £250 per week
2 Bed - Sleeps 4-6 - From only £350 per week

Image 1 Image 2 Image 3

- Fully Furnished Modern, Spacious & Comfortable Apartments
- Fully Staffed Development (Reception, Bar + Daily Cleaning)
- Family friendly & suitable for children of all ages

(Twitter Icon) @frostlodgevela
E-mail - frostlodgevela@mailbrook.co.uk
Telephone - +44 (0) 7700 913 284

Target Market(s)

Our target market is very wide. We are trying to attract students, couples and families who are skiing on a budget.

Industry/Entity Type

Accommodation

Requirements
Must have
• The text contained in 'task description' is important but i'd like to be led on design. Size of around 21.6 x 14cm is important and i'd like the 3 images below (hopefully someone can get of the date and time in orange bottom right of all pics)

http://img204.picvaultia.com/albums/qx512/tmrpics/Resort/318_00_640_kqra41c9.jpeg

http://img204.picvaultia.com/albums/qx512/tmrpics/Resort/b_02_kqrb6620.jpeg

http://img204.picvaultia.com/albums/qx512/tmrpics/Resort/318_08_640_kqrc93d7.jpeg

```html
<!DOCTYPE html>
<html lang="en">
<head>
<meta charset="utf-8">
<title>Luxury Self Catering Ski Apartments – Flyer</title>
<link href="https://fonts.googleapis.com/css2?family=Oswald:wght@300;500&family=Tinos:wght@400;700&family=Ubuntu:wght@700&family=Open+Sans:wght@400&display=swap" rel="stylesheet">
<style>
  :root{
    --page-bg:#e9e4dc;
    --maroon:#5a1518;
    --maroon-dark:#3f0d10;
    --maroon-light:#7a2327;
    --gold:#e2a64a;
    --gold-deep:#b77325;
    --cream:#f6e7c9;
    --cream-light:#fdf8ee;
    --ink:#4a1013;
    --white:#ffffff;
  }
  *{margin:0;padding:0;box-sizing:border-box}
  html,body{width:1200px;height:900px;overflow:hidden;background:var(--page-bg)}
  .flyer{
    position:absolute;left:305px;top:28px;width:543px;height:840px;overflow:hidden;
    background:linear-gradient(180deg,var(--cream) 50%,var(--cream-light) 85%);
    box-shadow:0 6px 18px rgba(0,0,0,.25);
  }
  .hero-photo{
    position:absolute;left:0;top:95px;width:543px;height:350px;
    background:linear-gradient(180deg,#f4f4f4 0%,#e8e6e3 30%,#b59a7c 60%,#7d6450 80%,#e9e9ea 100%);
  }
  .shapes{position:absolute;left:0;top:0}
  .headline{
    position:absolute;top:22px;left:0;width:100%;text-align:center;
    font-family:'Oswald',sans-serif;font-weight:500;font-size:27px;color:var(--gold);letter-spacing:.2px;
  }
  .subhead{
    position:absolute;top:58px;left:0;width:100%;text-align:center;
    font-family:'Oswald',sans-serif;font-weight:300;font-size:20px;color:var(--white);
  }
  .thumb{
    position:absolute;left:17px;width:143px;height:87px;
    border:4px solid var(--gold);box-shadow:0 2px 5px rgba(0,0,0,.35);
  }
  .thumb--bedroom{top:449px;background:linear-gradient(135deg,#c8a27a,#efe3d2 45%,#8a5b3a)}
  .thumb--lounge{top:557px;background:linear-gradient(135deg,#d9d4cb,#f2efea 50%,#5a4536)}
  .thumb--kitchen{top:664px;background:linear-gradient(135deg,#3b302b,#d8d2c9 55%,#5a3b2a)}
  .info{position:absolute;left:180px;top:434px;width:350px;color:var(--ink)}
  .info__place{text-align:center;font-family:'Ubuntu',sans-serif;font-weight:700;font-size:25px;margin-left:-10px}
  .info__source{text-align:center;font-family:'Ubuntu',sans-serif;font-weight:700;font-size:13px;margin-top:-2px;margin-left:-10px}
  .info__award{text-align:center;font-family:'Ubuntu',sans-serif;font-weight:700;font-size:14.5px;margin-left:-10px;white-space:nowrap}
  .quote{font-family:'Tinos',serif;margin-left:3px;margin-top:12px}
  .quote__source{font-weight:700;font-size:16px}
  .quote__text{font-size:14.5px;line-height:17px;margin-top:2px}
  .features{list-style:none;font-family:'Tinos',serif;font-size:14.5px;line-height:17px;margin-top:14px;margin-left:3px}
  .features li{position:relative;padding-left:18px;margin-bottom:3px}
  .features li::before{content:"";position:absolute;left:0;top:4px;border-left:11px solid var(--ink);border-top:5px solid transparent;border-bottom:5px solid transparent}
  .prices{margin-top:14px}
  .prices li{margin-bottom:4px}
  .prices b{font-family:'Ubuntu',sans-serif;font-size:15px}
  .contact{position:absolute;left:30px;top:776px;font-family:'Open Sans',sans-serif;color:var(--white);font-size:14px;line-height:20px}
  .contact__title{margin-left:23px}
  .contact__row{display:flex;align-items:center;gap:8px}
  .contact__icon{width:14px;height:14px;flex:none}
  .contact__social{display:inline-flex;align-items:center;gap:6px;margin-left:10px}
  .contact__square{width:12px;height:12px;background:var(--gold);display:inline-block}
</style>
</head>
<body>
<main class="flyer">
  <div class="hero-photo" role="img" aria-label="Photo of the snow-covered stone and white apartment building in winter"></div>

  <svg class="shapes" width="543" height="840" viewBox="0 0 543 840" aria-hidden="true">
    <defs>
      <linearGradient id="maroonFill" x1="0" y1="0" x2="0" y2="1">
        <stop offset="0" stop-color="var(--maroon-dark)"/>
        <stop offset="1" stop-color="var(--maroon-light)"/>
      </linearGradient>
      <linearGradient id="creamFill" x1="0" y1="0" x2="0" y2="1">
        <stop offset="0" stop-color="#efd3a4"/>
        <stop offset=".25" stop-color="var(--cream)"/>
        <stop offset="1" stop-color="var(--cream-light)"/>
      </linearGradient>
    </defs>
    <!-- header band -->
    <path d="M0,0 H543 V70 C470,100 400,115 300,118 C190,122 90,135 0,172 Z" fill="url(#maroonFill)"/>
    <path d="M130,128 C250,112 380,112 470,88 C500,80 525,70 543,62 V78 C500,98 440,112 330,120 C250,126 190,128 130,128 Z" fill="var(--gold)"/>
    <!-- cream body with wave -->
    <path d="M0,440 C80,410 180,400 300,405 C400,408 480,395 543,372 V840 H0 Z" fill="url(#creamFill)"/>
    <path d="M0,440 C80,412 170,404 280,406 C180,412 90,425 20,445 Z" fill="var(--gold)"/>
    <path d="M260,406 C380,410 470,398 543,372 V382 C470,405 380,414 260,406 Z" fill="var(--gold-deep)"/>
    <!-- footer band -->
    <path d="M0,772 C120,755 260,760 380,770 C450,775 500,772 543,765 V840 H0 Z" fill="url(#maroonFill)"/>
    <path d="M0,772 C120,755 260,760 380,770 C450,775 500,772 543,765 V770 C500,777 450,779 380,774 C260,764 120,760 0,776 Z" fill="var(--gold)"/>
  </svg>

  <h1 class="headline">Luxury Self Catering Ski Apartments For Rent</h1>
  <p class="subhead">Located 200m from Gondola, Restaurants and Bars</p>

  <div class="thumb thumb--bedroom" role="img" aria-label="Photo of a bright apartment bedroom"></div>
  <div class="thumb thumb--lounge" role="img" aria-label="Photo of an apartment lounge with sofa"></div>
  <div class="thumb thumb--kitchen" role="img" aria-label="Photo of an open-plan kitchen and dining area"></div>

  <section class="info">
    <h2 class="info__place">Bansko - Bulgaria</h2>
    <p class="info__source">TravelRater</p>
    <p class="info__award">Best Value Ski Resort in Europe 2011 + 2012</p>
    <div class="quote">
      <p class="quote__source">The Daily Ledger</p>
      <p class="quote__text">Bansko has been transformed into a winter<br>destination that can truly compete with<br>the Alps - at a fraction of the cost.</p>
    </div>
    <ul class="features">
      <li>Fully Furnished Modern,<br>Spacious &amp; Comfortable Apartments</li>
      <li>Fully Staffed Development<br>(Reception, Bar + Daily Cleaning)</li>
      <li>Family friendly &amp; suitable for children of all ages</li>
    </ul>
    <ul class="features prices">
      <li>Studio - Sleeps 1- 2 - From only <b>£200</b> per week</li>
      <li>1 Bed - Sleeps 2 - 4 - From only <b>£250</b> per week</li>
      <li>2 Bed - Sleeps 4 - 6 - From only <b>£350</b> per week</li>
    </ul>
  </section>

  <footer class="contact">
    <p class="contact__title">CONTACT US :</p>
    <p class="contact__row">
      <svg class="contact__icon" viewBox="0 0 24 24"><path fill="var(--gold)" d="M6.6 10.8c1.4 2.8 3.8 5.1 6.6 6.6l2.2-2.2c.3-.3.7-.4 1-.2 1.1.4 2.3.6 3.6.6.6 0 1 .4 1 1V20c0 .6-.4 1-1 1C10.6 21 3 13.4 3 4c0-.6.4-1 1-1h3.5c.6 0 1 .4 1 1 0 1.3.2 2.5.6 3.6.1.3 0 .7-.2 1z"/></svg>
      +44 (0) 7700 913 284
    </p>
    <p class="contact__row">
      <svg class="contact__icon" viewBox="0 0 24 24"><rect x="2" y="5" width="20" height="14" fill="var(--gold)"/><path d="M2 5l10 8 10-8" fill="none" stroke="var(--maroon)" stroke-width="2"/></svg>
      frostlodgevela@mailbrook.co.uk
      <span class="contact__social"><span class="contact__square"></span>@frostlodgevela</span>
    </p>
  </footer>
</main>
</body>
</html>
```